Spirit Distillery needs website design for velmarstills.com

We are a spirit distillery located in Canberra, Australia. We are just about to begin production on our products: Gin, Coffee vodka, lemon myrtle vodka, and apple and cinnamon vodka.
Velmar is Ancient Greek Mythology meaning "elixir of the Gods" so Greek mythology incorporated in the website, as well as simple and user friendly layout and functionality would be great.
Pages would include:
Welcome page with links to:
Our Products (Gin, Coffee vodka, lemon myrtle vodka, and apple and cinnamon vodka)
Events (what events the distillery is attending or holding at the distillery site)
Shop (for bottle sales)
Stockists (where the bottles are sold)
Cocktail recipe page

```html
<!DOCTYPE html>
<html lang="en">
<head>
<meta charset="utf-8">
<title>Velmar Distillery – Home</title>
<link href="https://fonts.googleapis.com/css2?family=Poppins:wght@400;600;700&family=Libre+Baskerville&family=Open+Sans:wght@400;600&display=swap" rel="stylesheet">
<style>
:root{
  --stage:#bdbdbd;
  --orange:#f7760a;
  --gold:#c9a04a;
  --ink:#2b2b2b;
  --muted:#555;
  --soft:#f3f2ef;
  --modal:#7b4416;
  --yes:#19b51d;
  --no:#f21c0c;
}
*{box-sizing:border-box;margin:0;padding:0}
html,body{width:851px;height:1200px;overflow:hidden;background:var(--stage)}
body{position:relative;font-family:"Open Sans",Arial,sans-serif;color:var(--ink)}
.page{position:absolute;top:61px;width:650px;height:2059px;background:#fff;transform:scale(.524);transform-origin:0 0;overflow:hidden}
.page--home{left:59px}
.page--gate{left:452px}
.serif{font-family:"Libre Baskerville",Georgia,serif;font-weight:400}
.btn{position:absolute;background:var(--orange);color:#fff;border-radius:14px;font:600 7px/24px "Poppins",sans-serif;text-align:center;width:76px;height:24px}

.site-header{position:absolute;left:0;top:0;width:650px;height:50px;background:#fff}
.brand{position:absolute;left:62px;top:12px;display:flex;align-items:center;gap:6px;color:var(--gold);font:400 19px "Libre Baskerville",serif;letter-spacing:1px}
.brand-dot{width:26px;height:26px;border:1.5px solid var(--gold);border-radius:50%}
.nav{position:absolute;top:24px;left:276px;display:flex;gap:15px;font:400 7px "Open Sans",sans-serif;color:#333}
.nav .active{color:var(--orange)}
.nav-caret{position:absolute;left:283px;top:42px;width:0;height:0;border-left:5px solid transparent;border-right:5px solid transparent;border-bottom:8px solid var(--orange)}

.hero{position:absolute;left:0;top:50px;width:650px;height:321px;background:radial-gradient(circle at 55% 40%,#5a6e6c 0%,#1f2e33 45%,#0d1519 100%)}
.hero-title{position:absolute;left:60px;top:104px;color:#fff;font:700 27px/33px "Poppins",sans-serif;letter-spacing:.5px}
.hero .btn{left:60px;top:176px}
.social{position:absolute;left:605px;width:17px;height:17px;border:1px solid #fff;border-radius:50%}
.slider-arrow{position:absolute;top:284px;width:20px;height:20px;border-radius:50%;background:rgba(0,0,0,.55)}

.welcome-art{position:absolute;left:60px;top:432px;width:235px;height:231px}
.welcome-art div{position:absolute}
.welcome-title{position:absolute;left:333px;top:425px;font-size:16px;line-height:23px;color:#222}
.rule{position:absolute;left:333px;top:474px;width:62px;height:1px;background:var(--orange)}
.welcome-text{position:absolute;left:333px;top:488px;width:265px;font-size:6.4px;line-height:13px;color:#444}

.products{position:absolute;left:0;top:731px;width:650px;height:362px;background:var(--soft)}
.section-title{position:absolute;left:0;width:650px;text-align:center;font-size:16px;color:#222}
.filters{position:absolute;left:0;top:84px;width:650px;display:flex;justify-content:center;gap:17px;font:400 7px "Libre Baskerville",serif;color:#333}
.filters .on{color:var(--orange);text-decoration:underline}
.card{position:absolute;top:111px;width:169px;height:196px;background:#fff;overflow:hidden;text-align:center}
.bottle{position:absolute;left:66px;top:10px;width:38px;height:110px;border-radius:14px 14px 6px 6px}
.card-name{position:absolute;left:0;top:128px;width:169px;font:400 10px "Libre Baskerville",serif;color:#222}
.card-price{position:absolute;left:0;top:148px;width:169px;font:400 10px "Libre Baskerville",serif;color:var(--orange)}
.cart{position:absolute;left:57px;top:168px;width:56px;height:56px;border-radius:50%;background:var(--orange)}

.events-grid{position:absolute;left:60px;top:1188px;width:529px;height:410px;border:1px solid #e6e6e6}
.event-img{position:absolute;width:265px;height:205px}
.event-body{position:absolute;width:264px;height:205px;padding:25px 16px 0 16px}
.date{display:inline-block;background:var(--orange);color:#fff;font:400 6.5px/24px "Libre Baskerville",serif;padding:0 12px;height:24px}
.event-body h3{font:400 12px/15px "Open Sans",sans-serif;margin-top:12px;color:#222}
.event-body p{font-size:6px;line-height:12px;color:#444;margin-top:10px}
.learn{display:block;margin-top:9px;margin-left:4px;font:600 6.5px "Open Sans",sans-serif;color:var(--orange);text-decoration:underline}

.band{position:absolute;left:0;top:1697px;width:650px;height:213px;background:linear-gradient(135deg,#3b3a22 0%,#1c1f1b 45%,#2c2e22 100%)}
.band p{position:absolute;left:125px;top:48px;width:400px;text-align:center;color:#fff;font:400 9.5px/19px "Libre Baskerville",serif}
.band .btn{left:287px;top:133px}

.footer{position:absolute;left:0;top:1910px;width:650px;height:149px;background:#fff}
.f-brand{position:absolute;left:60px;top:32px;text-align:center;color:var(--gold);font:400 19px "Libre Baskerville",serif;letter-spacing:1px}
.f-brand .brand-dot{margin:0 auto 4px;width:30px;height:30px}
.f-copy{position:absolute;left:60px;top:96px;font-size:6px;line-height:11px;color:#555}
.f-col{position:absolute;top:45px;font-size:6px;line-height:14px;color:#555}
.f-col h4{font:600 6.5px "Open Sans",sans-serif;color:#333;margin-bottom:2px}
.f-row{display:flex;align-items:center;gap:8px}
.ico{width:6px;height:6px;border-radius:50%;background:var(--orange)}

.veil{position:absolute;inset:0;background:rgba(40,40,40,.58)}
.age-gate{position:absolute;left:129px;top:131px;width:391px;height:194px;background:var(--modal);text-align:center;color:#fff}
.age-mark{width:56px;height:56px;border:2px solid var(--gold);border-radius:50%;margin:17px auto 0}
.age-kicker{font:600 7px "Poppins",sans-serif;margin-top:14px}
.age-q{font:700 21px "Poppins",sans-serif;margin-top:2px}
.age-actions{display:flex;justify-content:center;gap:6px;margin-top:6px}
.age-actions span{width:63px;height:22px;border-radius:11px;font:700 7.5px/22px "Poppins",sans-serif}
.yes{background:var(--yes)}.no{background:var(--no)}
</style>
</head>
<body>

<section class="page page--home">
  <header class="site-header">
    <div class="brand"><span class="brand-dot"></span>VELMAR</div>
    <nav class="nav"><span class="active">HOME</span><span>OUR PRODUCTS</span><span>EVENTS</span><span>SHOP</span><span>STOCKISTS</span><span>COCKTAIL RECIPE</span></nav>
    <div class="nav-caret"></div>
  </header>
  <div class="hero" role="img" aria-label="Cocktail glass with lime, mint and berries beside a shaker on a dark background">
    <h1 class="hero-title">VELMAR<br>DISTILLERY</h1>
    <span class="btn">READ MORE</span>
    <span class="social" style="top:115px"></span><span class="social" style="top:140px"></span><span class="social" style="top:165px"></span><span class="social" style="top:190px"></span>
    <span class="slider-arrow" style="left:298px"></span><span class="slider-arrow" style="left:332px"></span>
  </div>
  <div class="welcome-art">
    <div role="img" aria-label="Painting of a Greek god with a thunderbolt" style="left:0;top:19px;width:95px;height:140px;background:linear-gradient(160deg,#3b3f6e,#1e2238)"></div>
    <div role="img" aria-label="Painting of a goddess in golden armour" style="left:74px;top:0;width:112px;height:107px;background:linear-gradient(150deg,#f0b24a,#a84a18)"></div>
    <div role="img" aria-label="Bronze statue of a goddess holding a sphere" style="left:71px;top:108px;width:83px;height:123px;background:linear-gradient(180deg,#e8e5e0,#8a8178)"></div>
    <div role="img" aria-label="White marble statue of a robed goddess" style="left:155px;top:45px;width:80px;height:165px;background:linear-gradient(180deg,#fafafa,#c9c9c9)"></div>
  </div>
  <h2 class="welcome-title serif">WELCOME TO<br>VELMAR DISTILLERY</h2>
  <div class="rule"></div>
  <p class="welcome-text">Lorem ipsum dolor sit amet, consectetur adipiscing elit, sed do eiusmod tempor incididunt ut labore et dolore magna aliqua. Ut enim ad minim veniam, quis nostrud exercitation ullamco laboris nisi ut aliquip ex ea commodo consequat. Duis aute irure dolor in reprehenderit in voluptate velit esse cillum dolore eu fugiat nulla pariatur. Excepteur sint occaecat cupidatat non proident, sunt in culpa qui officia deserunt mollit anim id est laborum. Lorem ipsum dolor sit amet, consectetur adipiscing elit, sed do eiusmod tempor incididunt ut labore et dolore magna aliqua. Ut enim ad minim veniam, quis nostrud exercitation ullamco laboris nisi ut aliquip ex ea commodo consequat. Duis aute irure dolor in reprehenderit in voluptate velit esse cillum dolore eu fugiat nulla pariatur. Excepteur sint occaecat cupidatat non proident, sunt in culpa qui officia deserunt mollit anim id est laborum.</p>
  <span class="btn" style="left:332px;top:654px">READ MORE</span>

  <section class="products">
    <h2 class="section-title serif" style="top:52px">OUR PRODUCTS</h2>
    <div class="filters"><span class="on">ALL</span><span>GIN</span><span>COFFEE VODKA</span><span>LEMON MYRTLE VODKA</span><span>APPLE</span><span>CINNAMON VODKA</span></div>
    <div class="card" style="left:60px"><div class="bottle" role="img" aria-label="Amber spirit bottle" style="background:linear-gradient(180deg,#8a4a22,#c98b55 60%,#6b3a1a)"></div><div class="card-name">Nemo enim ipsam</div><div class="card-price">$25.00</div><div class="cart"></div></div>
    <div class="card" style="left:240px"><div class="bottle" role="img" aria-label="Clear gin bottle" style="background:linear-gradient(180deg,#e9edef,#c6c9c8 60%,#b99d6a)"></div><div class="card-name">Nemo enim ipsam</div><div class="card-price">$25.00</div><div class="cart"></div></div>
    <div class="card" style="left:420px"><div class="bottle" role="img" aria-label="Pale gold vodka bottle" style="background:linear-gradient(180deg,#d8c98a,#e7d9a4 60%,#b9a162)"></div><div class="card-name">Nemo enim ipsam</div><div class="card-price">$25.00</div><div class="cart"></div></div>
  </section>

  <h2 class="section-title serif" style="top:1146px">LATEST EVENTS</h2>
  <div class="events-grid">
    <div class="event-img" role="img" aria-label="Ancient Greek vase painting of warriors in black on orange" style="left:0;top:0;background:linear-gradient(135deg,#e08a2c,#2a1a10 50%,#d2792a)"></div>
    <div class="event-body" style="left:265px;top:0"><span class="date">Jan 20,2021</span><h3>Lorem ipsum dolor sit amet, conse ctetur adipiscing</h3><p>Lorem ipsum dolor sit amet, consectetur adipiscing elit, sed do eiusmod tempor incididunt ut labore et dolore magna aliqua. Ut enim ad minim veniam, quis nostrud exercitation ullamco laboris nisi ut aliquip ex ea commodo consequat. Duis aute irure dolor in reprehenderit in voluptate velit esse cillum dolore</p><span class="learn">Learn more →</span></div>
    <div class="event-body" style="left:0;top:205px"><span class="date">Jan 20,2021</span><h3>Lorem ipsum dolor sit amet, conse ctetur adipiscing</h3><p>Lorem ipsum dolor sit amet, consectetur adipiscing elit, sed do eiusmod tempor incididunt ut labore et dolore magna aliqua. Ut enim ad minim veniam, quis nostrud exercitation ullamco laboris nisi ut aliquip ex ea commodo consequat. Duis aute irure dolor in reprehenderit in voluptate velit esse cillum dolore</p><span class="learn">Learn more →</span></div>
    <div class="event-img" role="img" aria-label="Gin and tonic with ice and lime beside a bottle on a dark bar" style="left:264px;top:205px;background:linear-gradient(135deg,#2a2f33,#8d9aa0 50%,#1d2225)"></div>
  </div>
  <span class="btn" style="left:287px;top:1616px">VIEW MORE</span>

  <section class="band" role="img" aria-label="Tequila shots with salt rims and lime wedges">
    <p>Lorem ipsum dolor sit amet, consectetur adipiscing elit, sed do eiusmod tempor incididunt ut labore et dolore magna aliqua. Ut enim ad minim veniam, quis nostrud exercitation ullamco laboris nisi ut aliquip ex ea commodo consequat. Duis aute irure dolor in reprehenderit in voluptate velit esse cillum dolore</p>
    <span class="btn">VIEW MORE</span>
  </section>

  <footer class="footer">
    <div class="f-brand"><div class="brand-dot"></div>VELMAR</div>
    <div class="f-copy">Copyright 2021 Velmar Stills<br>All Right Reserved</div>
    <div class="f-col" style="left:218px"><h4>SITE MAP</h4>Home<br>About Us<br>Events<br>Gallery</div>
    <div class="f-col" style="left:268px;top:59px">Reviews<br>Blog<br>Contact Us</div>
    <div class="f-col" style="left:362px"><h4>CONTACT INFO</h4>Lorem ipsum dolor sit amet, consec<br>tetur adipiscing<div class="f-row"><span class="ico"></span>+61 2 5550 0142</div><div class="f-row"><span class="ico"></span>info@velmarstills.com</div></div>
    <div class="f-col" style="left:539px;line-height:19px"><h4>FOLLOW US</h4><div class="f-row"><span class="ico"></span>Friendbook</div><div class="f-row"><span class="ico"></span>Chirper</div><div class="f-row"><span class="ico"></span>Linkwork</div></div>
  </footer>
</section>

<section class="page page--gate">
  <header class="site-header">
    <div class="brand"><span class="brand-dot"></span>VELMAR</div>
    <nav class="nav"><span class="active">HOME</span><span>OUR PRODUCTS</span><span>EVENTS</span><span>SHOP</span><span>STOCKISTS</span><span>COCKTAIL RECIPE</span></nav>
    <div class="nav-caret"></div>
  </header>
  <div class="hero" role="img" aria-label="Cocktail glass with lime, mint and berries beside a shaker on a dark background">
    <h1 class="hero-title">VELMAR<br>DISTILLERY</h1>
    <span class="btn">READ MORE</span>
    <span class="social" style="top:115px"></span><span class="social" style="top:140px"></span><span class="social" style="top:165px"></span><span class="social" style="top:190px"></span>
    <span class="slider-arrow" style="left:298px"></span><span class="slider-arrow" style="left:332px"></span>
  </div>
  <div class="welcome-art">
    <div role="img" aria-label="Painting of a Greek god with a thunderbolt" style="left:0;top:19px;width:95px;height:140px;background:linear-gradient(160deg,#3b3f6e,#1e2238)"></div>
    <div role="img" aria-label="Painting of a goddess in golden armour" style="left:74px;top:0;width:112px;height:107px;background:linear-gradient(150deg,#f0b24a,#a84a18)"></div>
    <div role="img" aria-label="Bronze statue of a goddess holding a sphere" style="left:71px;top:108px;width:83px;height:123px;background:linear-gradient(180deg,#e8e5e0,#8a8178)"></div>
    <div role="img" aria-label="White marble statue of a robed goddess" style="left:155px;top:45px;width:80px;height:165px;background:linear-gradient(180deg,#fafafa,#c9c9c9)"></div>
  </div>
  <h2 class="welcome-title serif">WELCOME TO<br>VELMAR DISTILLERY</h2>
  <div class="rule"></div>
  <p class="welcome-text">Lorem ipsum dolor sit amet, consectetur adipiscing elit, sed do eiusmod tempor incididunt ut labore et dolore magna aliqua. Ut enim ad minim veniam, quis nostrud exercitation ullamco laboris nisi ut aliquip ex ea commodo consequat. Duis aute irure dolor in reprehenderit in voluptate velit esse cillum dolore eu fugiat nulla pariatur. Excepteur sint occaecat cupidatat non proident, sunt in culpa qui officia deserunt mollit anim id est laborum. Lorem ipsum dolor sit amet, consectetur adipiscing elit, sed do eiusmod tempor incididunt ut labore et dolore magna aliqua. Ut enim ad minim veniam, quis nostrud exercitation ullamco laboris nisi ut aliquip ex ea commodo consequat. Duis aute irure dolor in reprehenderit in voluptate velit esse cillum dolore eu fugiat nulla pariatur. Excepteur sint occaecat cupidatat non proident, sunt in culpa qui officia deserunt mollit anim id est laborum.</p>
  <span class="btn" style="left:332px;top:654px">READ MORE</span>

  <section class="products">
    <h2 class="section-title serif" style="top:52px">OUR PRODUCTS</h2>
    <div class="filters"><span class="on">ALL</span><span>GIN</span><span>COFFEE VODKA</span><span>LEMON MYRTLE VODKA</span><span>APPLE</span><span>CINNAMON VODKA</span></div>
    <div class="card" style="left:60px"><div class="bottle" role="img" aria-label="Amber spirit bottle" style="background:linear-gradient(180deg,#8a4a22,#c98b55 60%,#6b3a1a)"></div><div class="card-name">Nemo enim ipsam</div><div class="card-price">$25.00</div><div class="cart"></div></div>
    <div class="card" style="left:240px"><div class="bottle" role="img" aria-label="Clear gin bottle" style="background:linear-gradient(180deg,#e9edef,#c6c9c8 60%,#b99d6a)"></div><div class="card-name">Nemo enim ipsam</div><div class="card-price">$25.00</div><div class="cart"></div></div>
    <div class="card" style="left:420px"><div class="bottle" role="img" aria-label="Pale gold vodka bottle" style="background:linear-gradient(180deg,#d8c98a,#e7d9a4 60%,#b9a162)"></div><div class="card-name">Nemo enim ipsam</div><div class="card-price">$25.00</div><div class="cart"></div></div>
  </section>

  <h2 class="section-title serif" style="top:1146px">LATEST EVENTS</h2>
  <div class="events-grid">
    <div class="event-img" role="img" aria-label="Ancient Greek vase painting of warriors in black on orange" style="left:0;top:0;background:linear-gradient(135deg,#e08a2c,#2a1a10 50%,#d2792a)"></div>
    <div class="event-body" style="left:265px;top:0"><span class="date">Jan 20,2021</span><h3>Lorem ipsum dolor sit amet, conse ctetur adipiscing</h3><p>Lorem ipsum dolor sit amet, consectetur adipiscing elit, sed do eiusmod tempor incididunt ut labore et dolore magna aliqua. Ut enim ad minim veniam, quis nostrud exercitation ullamco laboris nisi ut aliquip ex ea commodo consequat. Duis aute irure dolor in reprehenderit in voluptate velit esse cillum dolore</p><span class="learn">Learn more →</span></div>
    <div class="event-body" style="left:0;top:205px"><span class="date">Jan 20,2021</span><h3>Lorem ipsum dolor sit amet, conse ctetur adipiscing</h3><p>Lorem ipsum dolor sit amet, consectetur adipiscing elit, sed do eiusmod tempor incididunt ut labore et dolore magna aliqua. Ut enim ad minim veniam, quis nostrud exercitation ullamco laboris nisi ut aliquip ex ea commodo consequat. Duis aute irure dolor in reprehenderit in voluptate velit esse cillum dolore</p><span class="learn">Learn more →</span></div>
    <div class="event-img" role="img" aria-label="Gin and tonic with ice and lime beside a bottle on a dark bar" style="left:264px;top:205px;background:linear-gradient(135deg,#2a2f33,#8d9aa0 50%,#1d2225)"></div>
  </div>
  <span class="btn" style="left:287px;top:1616px">VIEW MORE</span>

  <section class="band" role="img" aria-label="Tequila shots with salt rims and lime wedges">
    <p>Lorem ipsum dolor sit amet, consectetur adipiscing elit, sed do eiusmod tempor incididunt ut labore et dolore magna aliqua. Ut enim ad minim veniam, quis nostrud exercitation ullamco laboris nisi ut aliquip ex ea commodo consequat. Duis aute irure dolor in reprehenderit in voluptate velit esse cillum dolore</p>
    <span class="btn">VIEW MORE</span>
  </section>

  <footer class="footer">
    <div class="f-brand"><div class="brand-dot"></div>VELMAR</div>
    <div class="f-copy">Copyright 2021 Velmar Stills<br>All Right Reserved</div>
    <div class="f-col" style="left:218px"><h4>SITE MAP</h4>Home<br>About Us<br>Events<br>Gallery</div>
    <div class="f-col" style="left:268px;top:59px">Reviews<br>Blog<br>Contact Us</div>
    <div class="f-col" style="left:362px"><h4>CONTACT INFO</h4>Lorem ipsum dolor sit amet, consec<br>tetur adipiscing<div class="f-row"><span class="ico"></span>+61 2 5550 0142</div><div class="f-row"><span class="ico"></span>info@velmarstills.com</div></div>
    <div class="f-col" style="left:539px;line-height:19px"><h4>FOLLOW US</h4><div class="f-row"><span class="ico"></span>Friendbook</div><div class="f-row"><span class="ico"></span>Chirper</div><div class="f-row"><span class="ico"></span>Linkwork</div></div>
  </footer>

  <div class="veil"></div>
  <div class="age-gate">
    <div class="age-mark"></div>
    <p class="age-kicker">WE NEED TO VERIFY YOUR AGE</p>
    <p class="age-q">ARE YOU 18 OR OLDER?</p>
    <div class="age-actions"><span class="yes">YES</span><span class="no">NO</span></div>
  </div>
</section>

</body>
</html>
```